Online Defensive Driving Course Looking For Creativity!

Online defensive driving school looking for interesting, eye-catching multi-media (image or animated) ad options for future advertising efforts. These ads will be used in re-marketing campaigns trying to win back customers who have already visited then left the site and can include an upgrade promotional code to entice them back.

We are unsure if we would like to go with an ad that is cohesive with our branding on-site, as this creates a familiarity for the user but limits design creativity for ads. We would like to see interesting brand-cohesive options along with fun, creative, eye-catching options that might not necessarily fit with the brand image on the page.

Company is Maplecrest Driving School at MaplecrestDrivingSchool.com - http://www.maplecrestdrivingschool.com/defensive-driving/index.aspx?rr=dc
Product is Harwick Defensive Driving, which is a course used to remove points from Texas traffic tickets.

Key Ideas
(all key ideas are optional and not all need to be reflected in each ad version - use your judgement based on your ad concept)
Free Audio Upgrade - Use promo code XYZ
No Final Exam
SRB-Approved

Correct terminology for Texas is "defensive driving" and not "traffic school" or "driving school" so please use "defensive driving" in your ad.

For sizes, please choose a standard ad size - either a leaderboard size (728x90) or medium rectangle (300x250) or wide skyscraper (160x600).

Industry/Entity Type

Driving School

Font styles to use
Sans Serif

Colors

Designer to choose colors to be used in the design.

Requirements
Should not have
• "Traffic school", "driving school".

```html
<!DOCTYPE html>
<html lang="en">
<head>
<meta charset="utf-8">
<title>Maplecrest Driving School – Remarketing Banners</title>
<link rel="stylesheet" href="https://fonts.googleapis.com/css2?family=Lato:wght@700;900&display=swap">
<style>
  :root {
    --stage-light: #c9c9c9;
    --stage-dark: #6f6f6f;
    --frame: #ffffff;
    --headline: #ffffff;
    --promo: #1cb3f2;
    --cta: #fdaa0f;
    --cta-edge: #c9830a;
    --cta-text: #ffffff;
    --brand: #1d2a4f;
    --brand-mark: #c62828;
    --photo-sky: #a9c4dc;
    --photo-leaf: #4c6b3a;
    --photo-road: #4a4d52;
    --photo-hood: #b3261e;
  }
  * { box-sizing: border-box; margin: 0; padding: 0; }
  html, body { width: 1200px; height: 804px; overflow: hidden; }
  body {
    position: relative;
    font-family: "Lato", Arial, sans-serif;
    background: radial-gradient(ellipse at 55% 45%, var(--stage-light) 0%, #a4a4a4 55%, var(--stage-dark) 100%);
  }
  .banner { position: absolute; background: var(--frame); }
  .photo {
    position: absolute;
    background:
      linear-gradient(180deg, rgba(0,0,0,0) 82%, var(--photo-hood) 92%),
      linear-gradient(180deg, var(--photo-sky) 0%, #7d9a6b 32%, var(--photo-leaf) 48%, var(--photo-road) 64%, #3d4045 80%);
    border-radius: 0 0 26px 0;
    overflow: hidden;
  }
  .photo--wide {
    background:
      linear-gradient(180deg, rgba(0,0,0,0) 55%, var(--photo-hood) 78%),
      linear-gradient(90deg, #3e4146 0%, #56595e 45%, #6c7a55 80%, var(--photo-leaf) 100%);
  }
  .headline {
    position: absolute;
    color: var(--headline);
    font-weight: 900;
    text-transform: uppercase;
    text-align: center;
    line-height: 1.07;
    letter-spacing: -0.3px;
    text-shadow: 0 1px 3px rgba(0,0,0,0.35);
  }
  .headline .code { color: var(--promo); }
  .cta {
    position: absolute;
    display: flex; align-items: center; justify-content: center;
    background: var(--cta);
    color: var(--cta-text);
    font-weight: 900;
    text-transform: uppercase;
    border-radius: 999px;
    box-shadow: 0 4px 0 var(--cta-edge);
  }
  .brand {
    position: absolute;
    display: flex; align-items: center;
    color: var(--brand);
    font-weight: 700;
    white-space: nowrap;
  }
  .brand-mark { background: var(--brand-mark); flex: none; }

  /* Wide skyscraper 160x600 */
  .banner--sky { left: 48px; top: 31px; width: 192px; height: 720px; }
  .banner--sky .photo { left: 10px; top: 9px; width: 172px; height: 553px; }
  .banner--sky .headline { left: 0; top: 115px; width: 172px; font-size: 26px; }
  .banner--sky .cta { left: 10px; top: 588px; width: 170px; height: 36px; font-size: 17px; }
  .banner--sky .brand { left: 8px; top: 678px; font-size: 10.5px; gap: 4px; }
  .banner--sky .brand-mark { width: 14px; height: 14px; }

  /* Medium rectangle 300x250 */
  .banner--rect { left: 259px; top: 324px; width: 360px; height: 300px; }
  .banner--rect .photo { left: 10px; top: 10px; width: 340px; height: 224px; }
  .banner--rect .headline { left: 0; top: 70px; width: 340px; font-size: 27px; }
  .banner--rect .cta { left: 63px; top: 144px; width: 230px; height: 48px; font-size: 19px; }
  .banner--rect .brand { left: 24px; top: 248px; font-size: 19px; gap: 8px; }
  .banner--rect .brand-mark { width: 26px; height: 26px; }

  /* Leaderboard 728x90 */
  .banner--leader { left: 259px; top: 643px; width: 874px; height: 108px; }
  .banner--leader .brand { left: 12px; top: 8px; font-size: 19px; gap: 8px; }
  .banner--leader .brand-mark { width: 26px; height: 26px; }
  .banner--leader .cta { left: 48px; top: 44px; width: 229px; height: 50px; font-size: 19px; }
  .banner--leader .photo { left: 367px; top: 9px; width: 494px; height: 91px; }
  .banner--leader .headline { left: 0; top: 14px; width: 494px; font-size: 28px; }
</style>
</head>
<body>

  <section class="banner banner--sky" aria-label="Wide skyscraper ad">
    <div class="photo" role="img" aria-label="Country road lined with trees seen over the red hood of a car">
      <p class="headline">Free audio<br>upgrade<br>use promo<br>code <span class="code">XYZ</span></p>
    </div>
    <a class="cta">Learn more</a>
    <div class="brand"><span class="brand-mark"></span>MaplecrestDrivingSchool.com</div>
  </section>

  <section class="banner banner--rect" aria-label="Medium rectangle ad">
    <div class="photo" role="img" aria-label="Country road lined with trees seen over the red hood of a car">
      <p class="headline">Free audio upgrade<br>use promo code <span class="code">XYZ</span></p>
    </div>
    <a class="cta">Learn more</a>
    <div class="brand"><span class="brand-mark"></span>MaplecrestDrivingSchool.com</div>
  </section>

  <section class="banner banner--leader" aria-label="Leaderboard ad">
    <div class="brand"><span class="brand-mark"></span>MaplecrestDrivingSchool.com</div>
    <a class="cta">Learn more</a>
    <div class="photo photo--wide" role="img" aria-label="Road markings seen over the red hood of a car">
      <p class="headline">Free audio upgrade<br>use promo code <span class="code">XYZ</span></p>
    </div>
  </section>

</body>
</html>
```